1876 Basins & Spouts Business Card

I'm wanting to get a business card designed. Our business is 1876 Basins & Spouts
Details for the card:

1876 Basins & Spouts
Name: Harold Vesk
Email: harold@1876basinsandspouts.com.au
Website: www.1876basinsandspouts.com.au
Mobile: 0438 260 947
Phone: 02 7481 3926

Font of Basins & Spouts is called Snell Roundhand. Not sue what font logo text is.

I'm thinking two sided but it doesn't have to be.

```html
<!DOCTYPE html>
<html lang="en">
<head>
<meta charset="utf-8">
<title>1876 Basins &amp; Spouts Business Card</title>
<link rel="stylesheet" href="https://fonts.googleapis.com/css2?family=Roboto:wght@400;500;700&family=Poppins:wght@400;500&display=swap">
<style>
  :root {
    --ink: #000000;
    --paper: #ffffff;
    --backdrop: #e6e6e6;
    --muted: #6b6b6b;
    --text: #111111;
  }
  * { margin: 0; padding: 0; box-sizing: border-box; }
  html, body { width: 1200px; height: 1200px; overflow: hidden; }
  body { background: var(--backdrop); position: relative; font-family: "Roboto", Arial, sans-serif; }

  .card {
    position: absolute;
    left: 262px;
    width: 800px;
    height: 457px;
    transform: scale(0.8575);
    transform-origin: top left;
    background: var(--ink);
    overflow: hidden;
  }
  .card--front { top: 165px; }
  .card--back { top: 653px; }

  .front-panel { position: absolute; inset: 0; width: 800px; height: 457px; }

  .brand {
    position: absolute;
    left: 445px;
    top: 78px;
    width: 310px;
  }
  .brand-name {
    font-family: "Roboto", Arial, sans-serif;
    font-weight: 500;
    font-size: 22px;
    color: var(--text);
    display: flex;
    align-items: center;
    gap: 10px;
    white-space: nowrap;
  }
  .brand-dot {
    width: 12px; height: 12px; border-radius: 50%;
    background: var(--text);
    flex: none;
  }
  .brand-tagline {
    margin-top: 10px;
    font-size: 9.5px;
    color: var(--muted);
    letter-spacing: 0.2px;
    white-space: nowrap;
  }

  .holder-name {
    position: absolute;
    left: 57px;
    top: 278px;
    font-size: 28px;
    font-weight: 700;
    color: var(--text);
  }

  .contact {
    position: absolute;
    top: 342px;
    display: flex;
    flex-direction: column;
    gap: 5px;
    font-size: 19.5px;
    color: var(--text);
  }
  .contact--phones { left: 57px; }
  .contact--online { left: 260px; top: 340px; gap: 3px; }
  .contact-line { display: flex; align-items: center; gap: 12px; height: 22px; white-space: nowrap; }
  .contact-icon { width: 17px; height: 17px; flex: none; }

  .contact-divider {
    position: absolute;
    left: 233px;
    top: 343px;
    width: 2px;
    height: 44px;
    background: var(--text);
  }

  .back-brand {
    position: absolute;
    left: 0; right: 0;
    top: 188px;
    text-align: center;
    font-family: "Roboto", Arial, sans-serif;
    font-weight: 500;
    font-size: 40px;
    color: var(--paper);
  }
  .back-web {
    position: absolute;
    left: 0; right: 0;
    top: 378px;
    text-align: center;
    font-family: "Poppins", Arial, sans-serif;
    font-size: 18px;
    letter-spacing: 3.4px;
    color: var(--paper);
  }
</style>
</head>
<body>

<section class="card card--front" aria-label="Business card front">
  <svg class="front-panel" viewBox="0 0 800 457" aria-hidden="true">
    <path d="M175 0 L800 0 L800 280 C775 375 710 435 628 457 L0 457 L0 170 C28 82 95 22 175 0 Z" fill="var(--paper)"/>
  </svg>

  <div class="brand">
    <div class="brand-name"><span class="brand-dot"></span>1876 Basins &amp; Spouts</div>
    <div class="brand-tagline">Classic bathroom fittings made for everyday living</div>
  </div>

  <h1 class="holder-name">Harold Vesk</h1>

  <div class="contact contact--phones">
    <div class="contact-line">
      <svg class="contact-icon" viewBox="0 0 24 24" aria-hidden="true"><path fill="currentColor" d="M6.6 10.8a15.1 15.1 0 0 0 6.6 6.6l2.2-2.2a1 1 0 0 1 1-.25 11.4 11.4 0 0 0 3.6.57 1 1 0 0 1 1 1V20a1 1 0 0 1-1 1A17 17 0 0 1 3 4a1 1 0 0 1 1-1h3.5a1 1 0 0 1 1 1c0 1.25.2 2.450.57 3.57a1 1 0 0 1-.25 1z"/></svg>
      <span>02 7481 3926</span>
    </div>
    <div class="contact-line">
      <svg class="contact-icon" viewBox="0 0 24 24" aria-hidden="true"><rect x="6" y="1.5" width="12" height="21" rx="2" fill="none" stroke="currentColor" stroke-width="2.4"/><rect x="10" y="18" width="4" height="1.8" fill="currentColor"/></svg>
      <span>0438 260 947</span>
    </div>
  </div>

  <div class="contact-divider"></div>

  <div class="contact contact--online">
    <div class="contact-line">
      <svg class="contact-icon" viewBox="0 0 24 24" aria-hidden="true"><path fill="currentColor" d="M3 5h18v14H3z"/><path fill="none" stroke="#fff" stroke-width="1.8" d="M3 6l9 7 9-7"/></svg>
      <span>harold@1876basinsandspouts.com.au</span>
    </div>
    <div class="contact-line">
      <svg class="contact-icon" viewBox="0 0 24 24" aria-hidden="true"><circle cx="12" cy="12" r="10" fill="currentColor"/><path fill="#fff" d="M7 7c2 0 3 1 3 3s-2 1-2 3 1 3 0 4c-2-1-3-3-3-5 0-2 0-4 2-5zm8 5c1 0 3 1 3 3-1 2-2 3-4 3 0-2 1-2 0-4 0-1 0-2 1-2z"/></svg>
      <span>www.1876basinsandspouts.com.au</span>
    </div>
  </div>
</section>

<section class="card card--back" aria-label="Business card back">
  <div class="back-brand">1876 Basins &amp; Spouts</div>
  <div class="back-web">www.1876basinsandspouts.com.au</div>
</section>

</body>
</html>
```